creation of a business card design for a company specializing in the creation...

I would like to create a design for a professional business card on a black background and with the company's colors (I am attaching some files: including the logo in horizontal and centered format, I am also attaching a recent project design a T-shirt, this is the one I chose to give you an idea of my preferences.

we are in the process of developing a new website design, it is still in the development phase but it can be viewed at the following address: www.vantrelmo.be to give you other ideas about the company
you will see for yourself the subject of my main activity: company specializing in the construction of stairs

I would like a business card that stands out from the rest with a unique design

here is the informations
Name: Lucien Barthel
Function: Manager
Address: Rue Moulinet du Parc 42
7180 La Louvière
telephone: +32 468 219 804
email: info@rx7p.be
website: rx7p. be
social networks: Facebook, YouTube, TikTok, Instagram

Target Market(s)

customer who wants to have a beautiful staircase built

Industry/Entity Type

contruction d'escalier

Contact Information for Business Card

Adresse. Numero de telephone, site web, le texte : "Createur d'escalier", logo recto-verso, icone des reseaux sociaux

Requirements
Must have
• the mention: Stair creator
Nice to have
• an illustration of a designer staircase
Should not have
• do not distort the logo

```html
<!DOCTYPE html>
<html lang="en">
<head>
<meta charset="utf-8">
<title>RX7P Business Card</title>
<link href="https://fonts.googleapis.com/css2?family=Open+Sans:wght@400;600;700&display=swap" rel="stylesheet">
<style>
  :root {
    --page-bg: #d9d4cc;
    --card-dark: #262626;
    --card-black: #000000;
    --teal: #5b8590;
    --sage: #7e9690;
    --address: #b9aa93;
    --contact: #a38e74;
    --icon: #4f5557;
    --light-text: #cfc6b8;
    --social: #6f7a7c;
    --diamond: rgba(255,255,255,0.045);
  }
  * { margin: 0; padding: 0; box-sizing: border-box; }
  html, body {
    width: 1200px; height: 1046px; overflow: hidden;
    background: var(--page-bg);
    font-family: "Open Sans", Arial, sans-serif;
  }
  .card {
    position: absolute; left: 50px; top: 223px;
    width: 1100px; height: 600px; border-radius: 40px; overflow: hidden;
    background: radial-gradient(ellipse 60% 90% at 8% 85%, var(--card-dark) 0%, #151515 45%, var(--card-black) 75%);
  }
  .decor-diamond { position: absolute; left: 560px; top: 170px; width: 460px; height: 290px; }
  .brand {
    position: absolute; left: 34px; top: 37px; width: 222px; height: 200px;
    display: flex; align-items: center; justify-content: center; gap: 14px;
  }
  .brand-dot { width: 46px; height: 46px; border-radius: 50%; background: var(--teal); }
  .brand-name { font-size: 44px; font-weight: 600; color: var(--sage); letter-spacing: 2px; }
  .address {
    position: absolute; left: 41px; top: 276px;
    font-size: 29px; line-height: 37px; color: var(--address);
  }
  .contacts { position: absolute; left: 37px; top: 452px; list-style: none; }
  .contacts li {
    display: flex; align-items: center; height: 37px;
    font-size: 29px; color: var(--contact);
  }
  .contacts svg { width: 26px; height: 26px; margin-right: 17px; }
  .identity { position: absolute; right: 50px; top: 258px; text-align: right; }
  .person-name { font-size: 50px; font-weight: 700; line-height: 62px; color: var(--sage); }
  .person-name .surname { color: var(--teal); }
  .person-role { font-size: 29px; font-weight: 600; color: var(--light-text); line-height: 40px; }
  .accent-bar { position: absolute; right: 0; top: 267px; width: 34px; height: 93px; background: var(--teal); }
  .social {
    position: absolute; right: 46px; top: 524px;
    display: flex; align-items: center; gap: 17px;
  }
  .social-label { font-size: 29px; color: var(--light-text); margin-right: 0; }
  .social-dot { width: 27px; height: 27px; border-radius: 50%; background: var(--social); }
</style>
</head>
<body>
  <div class="card">
    <svg class="decor-diamond" viewBox="0 0 460 290" aria-hidden="true">
      <polygon points="230,0 460,145 230,290 0,145" fill="var(--diamond)"/>
    </svg>

    <div class="brand">
      <span class="brand-dot"></span>
      <span class="brand-name">RX7P</span>
    </div>

    <p class="address">Rue Moulinet du Parc 42<br>7180 La Louvière</p>

    <ul class="contacts">
      <li>
        <svg viewBox="0 0 24 24" aria-hidden="true"><path fill="var(--icon)" d="M6.6 10.8a15.2 15.2 0 0 0 6.6 6.6l2.2-2.2a1 1 0 0 1 1-.25 11.4 11.4 0 0 0 3.6.57 1 1 0 0 1 1 1V20a1 1 0 0 1-1 1A17 17 0 0 1 3 4a1 1 0 0 1 1-1h3.5a1 1 0 0 1 1 1c0 1.25.2 2.45.57 3.57a1 1 0 0 1-.25 1z"/></svg>
        +32 468 219 804
      </li>
      <li>
        <svg viewBox="0 0 24 24" aria-hidden="true"><rect x="2" y="5" width="20" height="14" rx="1.5" fill="var(--icon)"/><path d="M3 6l9 7 9-7" fill="none" stroke="#1c1c1c" stroke-width="1.6"/></svg>
        info@rx7p.be
      </li>
      <li>
        <svg viewBox="0 0 24 24" aria-hidden="true"><circle cx="12" cy="12" r="10" fill="var(--icon)"/><path d="M2 12h20M12 2c3 3 3 17 0 20M12 2c-3 3-3 17 0 20" fill="none" stroke="#1c1c1c" stroke-width="1.2"/></svg>
        www.rx7p. be
      </li>
    </ul>

    <div class="identity">
      <h1 class="person-name">Lucien <span class="surname">Barthel</span></h1>
      <p class="person-role">Manager</p>
    </div>
    <div class="accent-bar"></div>

    <div class="social">
      <span class="social-label">Follow us:</span>
      <span class="social-dot"></span>
      <span class="social-dot"></span>
      <span class="social-dot"></span>
      <span class="social-dot"></span>
    </div>
  </div>
</body>
</html>
```